Customizable Form Generation Website

This will be a place for users to quickly generate numerous forms from a categorized list. As the forms are templates with field variables, the site must be able to substitute ‘real data’ for template variable data. This tool will allow for quick custom forms on-demand.

The landing page is attached. We need the User Experience and User Interface solved for us.

EXAMPLE:
——————————————————————-
Dear {{PatientFirstName}},

Please come back for an examination on {{SelectedDate}} with Doctor {{SelectedProvider}}.

Sincerely,

{{SelectedAuthor}}
——————————————————————-

Coming to the Forms Landing Page, the user will see the forms available to select. The user will then click to select a form.

At some point, the user must resolve the variables in the form. For instance, there are the following variables in the above example: PatientFirstName, SelectedDate, SelectedProvider, and SelectedAuthor. We must give the user a chance to select the values for these variables. Using a dropdown combobox will probably work for most. Getting a date selector will be required if the variable happens to contain the string 'date'.

Is it best to preselect common variables before opening the form, or is it best to dynamically scan the template, then give the user the option to give values to each variable found?

The design must include a way for users to upload additional forms. Forms will most probably be PDF, .DOC, .TXT files. This allows users to develop simple or fancy forms of their choosing., then simply drop them into the site for future use.

The design must include a way for users to create new forms. The form creation tool must present to the user the list of predefined variables like {{PatientLastName}} for easy insertion into the form writer. Anytime "{{}}" are used, developers will recognize that as a variable that needs to be resolved.

The forms will be separated into categories as follows:

OFFICE:
- Letterhead
- Sign-In Sheet
- Fax Cover Sheet
SCHEDULER:
- Appointment Reminder
- Missed Appointment Policy
PATIENT:
- Intake Form
- Patient Discharge
- Return to Work or School
- Excuse Slip
- Consent to Treat a Minor
- Verify Non-Pregnancy
RELEASE:
- Health Information Release Form
- X-Ray Release Form
CERTIFICATES:
- Certificate of Care
- Disability Certificate
INSURANCE:
- Authorization to Bill Insurance
- Assignment Authorization
OTHER:
- Free Massage
- Free Vitamins

The design must include a way to add/customize categories. Categories are for organizing the forms logically.

We welcome ANY questions to help understand the requirements.

Good luck!

Healthcare

3 page

• Must Follow TESSERA LAYOUT standards
• Great User Experience. Simple, Fast, Clever.
• nothing to add here

```html
<!DOCTYPE html>
<html lang="en">
<head>
<meta charset="utf-8">
<title>Forms App – Screen Overview</title>
<link href="https://fonts.googleapis.com/css2?family=Montserrat:wght@400;500;600;700;800&display=swap" rel="stylesheet">
<style>
:root{
  --bg:#5f5f5f;
  --sidebar:#0c2a4c;
  --sidebar-active:#1a4f7e;
  --topbar:#0a1628;
  --body:#e7e8f7;
  --card:#ffffff;
  --orange:#f25a0c;
  --ink:#1a1a1a;
  --muted:#444;
  --tile:#e6e6eb;
  --green:#2aa52a;
  --blue:#1f6bb5;
  --purple:#8a1fd8;
  --olive:#b7ac1c;
  --navy-btn:#0f4f7c;
  --crimson:#d4124f;
  --lime:#2bbb1c;
  --label-navy:#1e3a5f;
}
*{box-sizing:border-box;margin:0;padding:0}
html,body{width:843px;height:1200px;overflow:hidden}
body{background:var(--bg);font-family:'Montserrat',sans-serif;position:relative;color:var(--ink)}
.screen{position:absolute;width:687px;height:493px;background:var(--body);transform:scale(.524);transform-origin:0 0;overflow:hidden}
.sidebar{position:absolute;left:0;top:0;width:83px;height:100%;background:var(--sidebar)}
.nav-item{height:44px;display:flex;align-items:center;padding-left:15px;gap:9px;color:#fff;font-size:7.5px;font-weight:500;border-bottom:1px solid rgba(255,255,255,.04)}
.nav-item svg{width:9px;height:9px;fill:#fff}
.nav-item.active{background:var(--sidebar-active)}
.nav-item:first-child{height:53px;padding-top:9px}
.topbar{position:absolute;left:83px;top:0;right:0;height:56px;background:var(--topbar);color:#fff}
.app-title{position:absolute;left:23px;top:14px;font-size:20px;font-weight:800;letter-spacing:.2px}
.practice{position:absolute;left:273px;top:21px;font-size:10.5px;font-weight:500;display:flex;align-items:center;gap:8px}
.practice i{display:block;width:7px;height:10px;background:var(--orange);border-radius:1px}
.welcome{position:absolute;right:96px;top:14px;text-align:right;line-height:1}
.welcome small{display:block;font-size:7px;margin-bottom:3px}
.welcome b{font-size:10.5px;font-weight:700}
.avatar{position:absolute;left:517px;top:13px;width:28px;height:28px;border-radius:50%;background:radial-gradient(circle at 50% 40%,#c9a58a,#6b5444)}
.logout{position:absolute;left:578px;top:17px;width:16px;height:16px;fill:#fff}
.card{position:absolute;left:94px;top:67px;width:583px;height:349px;background:var(--card);border-radius:4px;box-shadow:0 1px 3px rgba(0,0,0,.08)}
.footer{position:absolute;left:83px;right:0;top:452px;text-align:center;font-size:7.5px;color:#333}
.crumb{position:absolute;left:12px;top:17px;font-size:9.5px;color:#333}
.tabs{position:absolute;left:13px;top:43px;display:flex;gap:4px}
.tab{position:relative;width:76px;height:65px;border:2px solid var(--orange);color:var(--orange);display:flex;flex-direction:column;align-items:center;padding-top:11px}
.tab svg{width:20px;height:20px}
.tab span{margin-top:9px;font-size:7.5px;font-weight:700;color:var(--ink)}
.tab.active{background:var(--orange);color:#fff}
.tab.active span{color:#fff}
.tab.active::after{content:"";position:absolute;left:50%;bottom:-8px;margin-left:-6px;border:6px solid transparent;border-top-color:var(--orange);border-bottom:0}
.pill{position:absolute;height:47px;border-radius:24px;color:#fff;font-size:10px;font-weight:700;display:flex;align-items:center;justify-content:center;gap:12px;letter-spacing:.2px}
.pill .dot{width:24px;height:24px;border-radius:50%;background:#fff;display:flex;align-items:center;justify-content:center}
.pill .dot svg{width:13px;height:13px}
.big-pill{position:absolute;left:106px;width:370px;height:68px;border-radius:34px;color:#fff;font-size:21px;font-weight:800;display:flex;align-items:center;padding-left:100px}
.big-pill svg{position:absolute;left:34px;top:14px;width:44px;height:40px;fill:#fff}
.tile{position:absolute;width:177px;background:var(--tile);border-radius:3px;text-align:center}
.tile h3{font-size:12px;font-weight:700;margin-top:32px}
.thumb{position:absolute}
.ins-card{position:absolute;top:137px;width:271px;height:187px;border:2px solid #ccc;border-radius:3px}
.ins-card .photo{position:absolute;left:7px;top:6px;right:7px;height:143px}
.ins-card p{position:absolute;left:0;right:0;top:160px;text-align:center;font-size:10px;font-weight:700;color:var(--label-navy);letter-spacing:.2px}
.ptile{position:absolute;width:177px;height:112px;background:var(--tile);border-radius:3px;display:flex;flex-direction:column;align-items:center;padding-top:18px;color:var(--orange)}
.ptile svg{width:24px;height:24px}
.ptile h4{color:var(--ink);font-size:12px;font-weight:700;text-align:center;line-height:1.3;margin-top:16px}
.field{position:absolute;top:169px;width:172px;height:33px;border:1px solid #ccc;border-radius:17px;font-size:10px;display:flex;align-items:center;justify-content:space-between;padding:0 16px 0 19px}
.field svg{width:8px;height:8px}
</style>
</head>
<body>

<svg width="0" height="0" style="position:absolute">
  <defs>
    <symbol id="i-office" viewBox="0 0 24 24"><g fill="none" stroke="currentColor" stroke-width="1.5"><rect x="6" y="2.5" width="12" height="19"/><path d="M9 6h2M13 6h2M9 9.5h2M13 9.5h2M9 13h2M13 13h2M10.5 21.5v-4h3v4"/></g></symbol>
    <symbol id="i-cal" viewBox="0 0 24 24"><g fill="none" stroke="currentColor" stroke-width="1.7"><rect x="4" y="5" width="16" height="16" rx="1"/><path d="M4 9h16M8 3v4M16 3v4M8.5 14.5l2.5 2.5 4.5-4.5"/></g></symbol>
    <symbol id="i-user" viewBox="0 0 24 24"><g fill="none" stroke="currentColor" stroke-width="1.7"><circle cx="12" cy="12" r="9"/><circle cx="12" cy="10" r="3.2"/><path d="M6.3 18.5c1.4-2.4 3.3-3.5 5.7-3.5s4.3 1.1 5.7 3.5"/></g></symbol>
    <symbol id="i-news" viewBox="0 0 24 24"><g fill="none" stroke="currentColor" stroke-width="1.5"><rect x="2.5" y="5" width="19" height="14"/><rect x="5.5" y="8" width="6" height="5"/><path d="M14 8.5h5M14 11h5M14 13.5h5M5.5 16h13.5"/></g></symbol>
    <symbol id="i-badge" viewBox="0 0 24 24"><path fill="currentColor" d="M12 2l2.1 2.2 3-.6.9 2.9 2.9.9-.6 3L22.5 12l-2.2 2.1.6 3-2.9.9-.9 2.9-3-.6L12 22.5l-2.1-2.2-3 .6-.9-2.9-2.9-.9.6-3L1.5 12l2.2-2.1-.6-3 2.9-.9.9-2.9 3 .6z"/></symbol>
    <symbol id="i-shield" viewBox="0 0 24 24"><path fill="currentColor" d="M12 2L4 5v6c0 5 3.4 9.4 8 11 4.6-1.6 8-6 8-11V5zm0 3.2l5 1.9v4.2c0 3.4-2.1 6.5-5 7.8z"/></symbol>
    <symbol id="i-list" viewBox="0 0 24 24"><path fill="currentColor" d="M2 4h20v2.5H2zM10 9h12v2.5H10zM10 13.5h12V16H10zM2 18h20v2.5H2zM2 9.2l5 2.8-5 2.8z"/></symbol>
    <symbol id="i-doc" viewBox="0 0 24 24"><g fill="none" stroke="currentColor" stroke-width="1.5"><path d="M5 2.5h9.5L19 7v14.5H5z"/><path d="M14.5 2.5V7H19M8 11h8M8 14h8M8 17h8"/></g></symbol>
    <symbol id="i-edit" viewBox="0 0 24 24"><g fill="none" stroke="currentColor" stroke-width="1.7"><path d="M18 13v7H4V6h7"/><path d="M16 3.5l4.5 4.5L12 16.5H7.5V12z"/></g></symbol>
    <symbol id="i-chart" viewBox="0 0 24 24"><g fill="none" stroke="currentColor" stroke-width="1.7"><path d="M3 3v18h18"/><path d="M6 16l5-5 3 3 6-6M16 8h4v4"/></g></symbol>
    <symbol id="i-thumb" viewBox="0 0 24 24"><path fill="currentColor" d="M2 10h4v11H2zM8 10l4-8c1.7 0 2.8 1.2 2.5 3L14 9h6c1.2 0 2 1 1.8 2.2l-1.5 8C20.1 20.3 19.3 21 18.2 21H8z"/></symbol>
    <symbol id="i-sq" viewBox="0 0 10 10"><rect x="1" y="1" width="8" height="8" rx="1.5"/></symbol>
  </defs>
</svg>

<!-- Screen 1: Forms entry -->
<section class="screen" style="left:54px;top:57px">
  <nav class="sidebar">
    <div class="nav-item"><svg><use href="#i-sq"/></svg>Home</div><div class="nav-item"><svg><use href="#i-sq"/></svg>Scheduler</div><div class="nav-item"><svg><use href="#i-sq"/></svg>Patients</div><div class="nav-item"><svg><use href="#i-sq"/></svg>Encounters</div><div class="nav-item"><svg><use href="#i-sq"/></svg>Payments</div><div class="nav-item"><svg><use href="#i-sq"/></svg>Billing</div><div class="nav-item"><svg><use href="#i-sq"/></svg>Reporting</div><div class="nav-item"><svg><use href="#i-sq"/></svg>Marketing</div><div class="nav-item active"><svg><use href="#i-sq"/></svg>Forms</div><div class="nav-item"><svg><use href="#i-sq"/></svg>Lists</div><div class="nav-item"><svg><use href="#i-sq"/></svg>Admin</div>
  </nav>
  <header class="topbar"><div class="app-title">Forms App</div><div class="practice"><i></i>Sample healthcare practice</div><div class="welcome"><small>Welcome</small><b>Back,Test</b></div><div class="avatar" role="img" aria-label="User profile photo"></div><svg class="logout" viewBox="0 0 24 24"><path d="M3 3h9v3H6v12h6v3H3zM14 6l6 6-6 6v-4H9v-4h5z"/></svg></header>
  <div class="card">
    <svg style="position:absolute;left:29px;top:31px;width:18px;height:16px" viewBox="0 0 18 16"><path fill="var(--orange)" d="M0 1h18v2.4H0zM0 6.8h18v2.4H0zM0 12.6h18V15H0z"/></svg>
    <div style="position:absolute;left:60px;top:27px;font-size:19px;font-weight:700">Forms</div>
    <div style="position:absolute;left:0;right:0;top:112px;text-align:center;font-size:21px;font-weight:700">John Doe</div>
    <div class="field" style="left:27px">Selected Date<svg viewBox="0 0 10 10"><rect x="1" y="2" width="8" height="7" fill="#222"/></svg></div>
    <div class="field" style="left:205px">Selected Provider<svg viewBox="0 0 10 10"><path d="M1.5 3l3.5 4 3.5-4" fill="none" stroke="#222" stroke-width="1.8"/></svg></div>
    <div class="field" style="left:383px">Selected Author<svg viewBox="0 0 10 10"><path d="M1.5 3l3.5 4 3.5-4" fill="none" stroke="#222" stroke-width="1.8"/></svg></div>
    <div class="pill" style="left:227px;top:234px;width:128px;height:43px;background:var(--orange);font-size:14px;border-radius:22px">SUBMIT</div>
  </div>
  <div class="footer">(c)2021 Companyname.All Rights Reserved &nbsp;|&nbsp; Privacy Policy &nbsp;|&nbsp; Terms and Use</div>
</section>

<!-- Screen 2: Release -->
<section class="screen" style="left:429px;top:57px">
  <nav class="sidebar">
    <div class="nav-item active"><svg><use href="#i-sq"/></svg>Home</div><div class="nav-item"><svg><use href="#i-sq"/></svg>Scheduler</div><div class="nav-item"><svg><use href="#i-sq"/></svg>Patients</div><div class="nav-item"><svg><use href="#i-sq"/></svg>Encounters</div><div class="nav-item"><svg><use href="#i-sq"/></svg>Payments</div><div class="nav-item"><svg><use href="#i-sq"/></svg>Billing</div><div class="nav-item"><svg><use href="#i-sq"/></svg>Reporting</div><div class="nav-item"><svg><use href="#i-sq"/></svg>Marketing</div><div class="nav-item"><svg><use href="#i-sq"/></svg>Forms</div><div class="nav-item"><svg><use href="#i-sq"/></svg>Lists</div><div class="nav-item"><svg><use href="#i-sq"/></svg>Admin</div>
  </nav>
  <header class="topbar"><div class="app-title">Forms App</div><div class="practice"><i></i>Sample healthcare practice</div><div class="welcome"><small>Welcome</small><b>Back,Test</b></div><div class="avatar" role="img" aria-label="User profile photo"></div><svg class="logout" viewBox="0 0 24 24"><path d="M3 3h9v3H6v12h6v3H3zM14 6l6 6-6 6v-4H9v-4h5z"/></svg></header>
  <div class="card">
    <div class="crumb">Home &nbsp;/&nbsp; Release</div>
    <div class="tabs">
      <div class="tab"><svg><use href="#i-office"/></svg><span>OFFICE</span></div><div class="tab"><svg><use href="#i-cal"/></svg><span>SCHEDULER</span></div><div class="tab"><svg><use href="#i-user"/></svg><span>PATIENT</span></div><div class="tab active"><svg><use href="#i-news"/></svg><span>RELEASE</span></div><div class="tab"><svg><use href="#i-badge"/></svg><span>CERTIFICATES</span></div><div class="tab"><svg><use href="#i-shield"/></svg><span>INSURANCE</span></div><div class="tab"><svg><use href="#i-list"/></svg><span>OTHER</span></div>
    </div>
    <div class="pill" style="left:33px;top:162px;width:254px;background:var(--green)">HEALTH INFORMATION RELEASE FORM</div>
    <div class="pill" style="left:296px;top:162px;width:253px;background:var(--blue)">X-RAY RELEASE FORM</div>
  </div>
  <div class="footer">(c)2021 Companyname.All Rights Reserved &nbsp;|&nbsp; Privacy Policy &nbsp;|&nbsp; Terms and Use</div>
</section>

<!-- Screen 3: Office -->
<section class="screen" style="left:54px;top:333.5px">
  <nav class="sidebar">
    <div class="nav-item active"><svg><use href="#i-sq"/></svg>Home</div><div class="nav-item"><svg><use href="#i-sq"/></svg>Scheduler</div><div class="nav-item"><svg><use href="#i-sq"/></svg>Patients</div><div class="nav-item"><svg><use href="#i-sq"/></svg>Encounters</div><div class="nav-item"><svg><use href="#i-sq"/></svg>Payments</div><div class="nav-item"><svg><use href="#i-sq"/></svg>Billing</div><div class="nav-item"><svg><use href="#i-sq"/></svg>Reporting</div><div class="nav-item"><svg><use href="#i-sq"/></svg>Marketing</div><div class="nav-item"><svg><use href="#i-sq"/></svg>Forms</div><div class="nav-item"><svg><use href="#i-sq"/></svg>Lists</div><div class="nav-item"><svg><use href="#i-sq"/></svg>Admin</div>
  </nav>
  <header class="topbar"><div class="app-title">Forms App</div><div class="practice"><i></i>Sample healthcare practice</div><div class="welcome"><small>Welcome</small><b>Back,Test</b></div><div class="avatar" role="img" aria-label="User profile photo"></div><svg class="logout" viewBox="0 0 24 24"><path d="M3 3h9v3H6v12h6v3H3zM14 6l6 6-6 6v-4H9v-4h5z"/></svg></header>
  <div class="card">
    <div class="crumb">Home &nbsp;/&nbsp; Office</div>
    <div class="tabs">
      <div class="tab active"><svg><use href="#i-office"/></svg><span>OFFICE</span></div><div class="tab"><svg><use href="#i-cal"/></svg><span>SCHEDULER</span></div><div class="tab"><svg><use href="#i-user"/></svg><span>PATIENT</span></div><div class="tab"><svg><use href="#i-news"/></svg><span>RELEASE</span></div><div class="tab"><svg><use href="#i-badge"/></svg><span>CERTIFICATES</span></div><div class="tab"><svg><use href="#i-shield"/></svg><span>INSURANCE</span></div><div class="tab"><svg><use href="#i-list"/></svg><span>OTHER</span></div>
    </div>
    <div class="tile" style="left:15px;top:139px;height:194px"><h3>Letterhead</h3>
      <div class="thumb" role="img" aria-label="Letterhead template preview" style="left:15px;top:72px;width:147px;height:94px;background:linear-gradient(90deg,#f4efe4 0 44%,transparent 44% 56%,#f4efe4 56%),linear-gradient(#2a2450,#e3b24a)"></div>
    </div>
    <div class="tile" style="left:203px;top:139px;height:194px"><h3>Sign-In Sheet</h3>
      <div class="thumb" role="img" aria-label="Sign-in sheet template preview" style="left:9px;top:70px;width:159px;height:106px;background:linear-gradient(90deg,#f7f7f9,#ececf0)"></div>
    </div>
    <div class="tile" style="left:390px;top:139px;height:194px"><h3>Fax Cover Sheet</h3>
      <div class="thumb" role="img" aria-label="Fax cover sheet template preview" style="left:10px;top:66px;width:158px;height:110px;background:radial-gradient(ellipse at 50% 50%,#e6c160 0 22%,#1f2328 48%)"></div>
    </div>
  </div>
  <div class="footer">(c)2021 Companyname.All Rights Reserved &nbsp;|&nbsp; Privacy Policy &nbsp;|&nbsp; Terms and Use</div>
</section>

<!-- Screen 4: Certificates -->
<section class="screen" style="left:429px;top:333.5px">
  <nav class="sidebar">
    <div class="nav-item active"><svg><use href="#i-sq"/></svg>Home</div><div class="nav-item"><svg><use href="#i-sq"/></svg>Scheduler</div><div class="nav-item"><svg><use href="#i-sq"/></svg>Patients</div><div class="nav-item"><svg><use href="#i-sq"/></svg>Encounters</div><div class="nav-item"><svg><use href="#i-sq"/></svg>Payments</div><div class="nav-item"><svg><use href="#i-sq"/></svg>Billing</div><div class="nav-item"><svg><use href="#i-sq"/></svg>Reporting</div><div class="nav-item"><svg><use href="#i-sq"/></svg>Marketing</div><div class="nav-item"><svg><use href="#i-sq"/></svg>Forms</div><div class="nav-item"><svg><use href="#i-sq"/></svg>Lists</div><div class="nav-item"><svg><use href="#i-sq"/></svg>Admin</div>
  </nav>
  <header class="topbar"><div class="app-title">Forms App</div><div class="practice"><i></i>Sample healthcare practice</div><div class="welcome"><small>Welcome</small><b>Back,Test</b></div><div class="avatar" role="img" aria-label="User profile photo"></div><svg class="logout" viewBox="0 0 24 24"><path d="M3 3h9v3H6v12h6v3H3zM14 6l6 6-6 6v-4H9v-4h5z"/></svg></header>
  <div class="card">
    <div class="crumb">Home &nbsp;/&nbsp; Certificates</div>
    <div class="tabs">
      <div class="tab"><svg><use href="#i-office"/></svg><span>OFFICE</span></div><div class="tab"><svg><use href="#i-cal"/></svg><span>SCHEDULER</span></div><div class="tab"><svg><use href="#i-user"/></svg><span>PATIENT</span></div><div class="tab"><svg><use href="#i-news"/></svg><span>RELEASE</span></div><div class="tab active"><svg><use href="#i-badge"/></svg><span>CERTIFICATES</span></div><div class="tab"><svg><use href="#i-shield"/></svg><span>INSURANCE</span></div><div class="tab"><svg><use href="#i-list"/></svg><span>OTHER</span></div>
    </div>
    <div class="pill" style="left:33px;top:162px;width:254px;background:var(--purple)"><span class="dot"><svg viewBox="0 0 24 24"><path fill="var(--purple)" d="M12 21l-8.5-8.6C1 9.8 2 5 6.5 4.5 9 4.3 11 6 12 7.5 13 6 15 4.3 17.5 4.5 22 5 23 9.8 20.5 12.4z"/></svg></span>CERTIFICATE OF CARE</div>
    <div class="pill" style="left:296px;top:162px;width:253px;background:var(--olive)"><span class="dot"><svg viewBox="0 0 24 24"><path fill="var(--olive)" d="M5 2h10l4 4v16H5z"/></svg></span>DISABILITY CERTIFICATE</div>
  </div>
  <div class="footer">(c)2021 Companyname.All Rights Reserved &nbsp;|&nbsp; Privacy Policy &nbsp;|&nbsp; Terms and Use</div>
</section>

<!-- Screen 5: Scheduler -->
<section class="screen" style="left:54px;top:610px">
  <nav class="sidebar">
    <div class="nav-item active"><svg><use href="#i-sq"/></svg>Home</div><div class="nav-item"><svg><use href="#i-sq"/></svg>Scheduler</div><div class="nav-item"><svg><use href="#i-sq"/></svg>Patients</div><div class="nav-item"><svg><use href="#i-sq"/></svg>Encounters</div><div class="nav-item"><svg><use href="#i-sq"/></svg>Payments</div><div class="nav-item"><svg><use href="#i-sq"/></svg>Billing</div><div class="nav-item"><svg><use href="#i-sq"/></svg>Reporting</div><div class="nav-item"><svg><use href="#i-sq"/></svg>Marketing</div><div class="nav-item"><svg><use href="#i-sq"/></svg>Forms</div><div class="nav-item"><svg><use href="#i-sq"/></svg>Lists</div><div class="nav-item"><svg><use href="#i-sq"/></svg>Admin</div>
  </nav>
  <header class="topbar"><div class="app-title">Forms App</div><div class="practice"><i></i>Sample healthcare practice</div><div class="welcome"><small>Welcome</small><b>Back,Test</b></div><div class="avatar" role="img" aria-label="User profile photo"></div><svg class="logout" viewBox="0 0 24 24"><path d="M3 3h9v3H6v12h6v3H3zM14 6l6 6-6 6v-4H9v-4h5z"/></svg></header>
  <div class="card">
    <div class="crumb">Home &nbsp;/&nbsp; Scheduler</div>
    <div class="tabs">
      <div class="tab"><svg><use href="#i-office"/></svg><span>OFFICE</span></div><div class="tab active"><svg><use href="#i-cal"/></svg><span>SCHEDULER</span></div><div class="tab"><svg><use href="#i-user"/></svg><span>PATIENT</span></div><div class="tab"><svg><use href="#i-news"/></svg><span>RELEASE</span></div><div class="tab"><svg><use href="#i-badge"/></svg><span>CERTIFICATES</span></div><div class="tab"><svg><use href="#i-shield"/></svg><span>INSURANCE</span></div><div class="tab"><svg><use href="#i-list"/></svg><span>OTHER</span></div>
    </div>
    <div class="pill" style="left:33px;top:162px;width:254px;background:var(--navy-btn)">APPOINTMENT REMINDER</div>
    <div class="pill" style="left:296px;top:162px;width:253px;background:var(--topbar)">MISSED APPOINTMENT POLICY</div>
  </div>
  <div class="footer">(c)2021 Companyname.All Rights Reserved &nbsp;|&nbsp; Privacy Policy &nbsp;|&nbsp; Terms and Use</div>
</section>

<!-- Screen 6: Insurance -->
<section class="screen" style="left:429px;top:610px">
  <nav class="sidebar">
    <div class="nav-item active"><svg><use href="#i-sq"/></svg>Home</div><div class="nav-item"><svg><use href="#i-sq"/></svg>Scheduler</div><div class="nav-item"><svg><use href="#i-sq"/></svg>Patients</div><div class="nav-item"><svg><use href="#i-sq"/></svg>Encounters</div><div class="nav-item"><svg><use href="#i-sq"/></svg>Payments</div><div class="nav-item"><svg><use href="#i-sq"/></svg>Billing</div><div class="nav-item"><svg><use href="#i-sq"/></svg>Reporting</div><div class="nav-item"><svg><use href="#i-sq"/></svg>Marketing</div><div class="nav-item"><svg><use href="#i-sq"/></svg>Forms</div><div class="nav-item"><svg><use href="#i-sq"/></svg>Lists</div><div class="nav-item"><svg><use href="#i-sq"/></svg>Admin</div>
  </nav>
  <header class="topbar"><div class="app-title">Forms App</div><div class="practice"><i></i>Sample healthcare practice</div><div class="welcome"><small>Welcome</small><b>Back,Test</b></div><div class="avatar" role="img" aria-label="User profile photo"></div><svg class="logout" viewBox="0 0 24 24"><path d="M3 3h9v3H6v12h6v3H3zM14 6l6 6-6 6v-4H9v-4h5z"/></svg></header>
  <div class="card">
    <div class="crumb">Home &nbsp;/&nbsp; Insurance</div>
    <div class="tabs">
      <div class="tab"><svg><use href="#i-office"/></svg><span>OFFICE</span></div><div class="tab"><svg><use href="#i-cal"/></svg><span>SCHEDULER</span></div><div class="tab"><svg><use href="#i-user"/></svg><span>PATIENT</span></div><div class="tab"><svg><use href="#i-news"/></svg><span>RELEASE</span></div><div class="tab"><svg><use href="#i-badge"/></svg><span>CERTIFICATES</span></div><div class="tab active"><svg><use href="#i-shield"/></svg><span>INSURANCE</span></div><div class="tab"><svg><use href="#i-list"/></svg><span>OTHER</span></div>
    </div>
    <div class="ins-card" style="left:17px"><div class="photo" role="img" aria-label="Photo of a past-due medical bill" style="background:linear-gradient(135deg,#9aa3ad,#e8edf3 55%,#b8c2cc)"></div><p>AUTHORIZATION TO BILL INSURANCE</p></div>
    <div class="ins-card" style="left:299px"><div class="photo" role="img" aria-label="Image of an assignment document heading" style="background:radial-gradient(ellipse at 50% 45%,#ffffff,#d6d8db)"></div><p>ASSIGNMENT AUTHORIZATION</p></div>
  </div>
  <div class="footer">(c)2021 Companyname.All Rights Reserved &nbsp;|&nbsp; Privacy Policy &nbsp;|&nbsp; Terms and Use</div>
</section>

<!-- Screen 7: Patient -->
<section class="screen" style="left:54px;top:887px">
  <nav class="sidebar">
    <div class="nav-item active"><svg><use href="#i-sq"/></svg>Home</div><div class="nav-item"><svg><use href="#i-sq"/></svg>Scheduler</div><div class="nav-item"><svg><use href="#i-sq"/></svg>Patients</div><div class="nav-item"><svg><use href="#i-sq"/></svg>Encounters</div><div class="nav-item"><svg><use href="#i-sq"/></svg>Payments</div><div class="nav-item"><svg><use href="#i-sq"/></svg>Billing</div><div class="nav-item"><svg><use href="#i-sq"/></svg>Reporting</div><div class="nav-item"><svg><use href="#i-sq"/></svg>Marketing</div><div class="nav-item"><svg><use href="#i-sq"/></svg>Forms</div><div class="nav-item"><svg><use href="#i-sq"/></svg>Lists</div><div class="nav-item"><svg><use href="#i-sq"/></svg>Admin</div>
  </nav>
  <header class="topbar"><div class="app-title">Forms App</div><div class="practice"><i></i>Sample healthcare practice</div><div class="welcome"><small>Welcome</small><b>Back,Test</b></div><div class="avatar" role="img" aria-label="User profile photo"></div><svg class="logout" viewBox="0 0 24 24"><path d="M3 3h9v3H6v12h6v3H3zM14 6l6 6-6 6v-4H9v-4h5z"/></svg></header>
  <div class="card" style="height:381px">
    <div class="crumb">Home &nbsp;/&nbsp; Patient</div>
    <div class="tabs">
      <div class="tab"><svg><use href="#i-office"/></svg><span>OFFICE</span></div><div class="tab"><svg><use href="#i-cal"/></svg><span>SCHEDULER</span></div><div class="tab active"><svg><use href="#i-user"/></svg><span>PATIENT</span></div><div class="tab"><svg><use href="#i-news"/></svg><span>RELEASE</span></div><div class="tab"><svg><use href="#i-badge"/></svg><span>CERTIFICATES</span></div><div class="tab"><svg><use href="#i-shield"/></svg><span>INSURANCE</span></div><div class="tab"><svg><use href="#i-list"/></svg><span>OTHER</span></div>
    </div>
    <div class="ptile" style="left:15px;top:131px"><svg><use href="#i-doc"/></svg><h4>Intake Form</h4></div>
    <div class="ptile" style="left:203px;top:131px"><svg><use href="#i-user"/></svg><h4>Patient Discharge</h4></div>
    <div class="ptile" style="left:390px;top:131px"><svg><use href="#i-office"/></svg><h4 style="margin-top:10px">Return to Work<br>or School</h4></div>
    <div class="ptile" style="left:15px;top:255px"><svg><use href="#i-edit"/></svg><h4>Excuse Slip</h4></div>
    <div class="ptile" style="left:203px;top:255px"><svg><use href="#i-chart"/></svg><h4>Consent to Treat<br>a Minor</h4></div>
    <div class="ptile" style="left:390px;top:255px"><svg><use href="#i-thumb"/></svg><h4>Verify<br>Non-Pregnancy</h4></div>
  </div>
  <div class="footer" style="top:468px">(c)2021 Companyname.All Rights Reserved &nbsp;|&nbsp; Privacy Policy &nbsp;|&nbsp; Terms and Use</div>
</section>

<!-- Screen 8: Other -->
<section class="screen" style="left:429px;top:887px">
  <nav class="sidebar">
    <div class="nav-item active"><svg><use href="#i-sq"/></svg>Home</div><div class="nav-item"><svg><use href="#i-sq"/></svg>Scheduler</div><div class="nav-item"><svg><use href="#i-sq"/></svg>Patients</div><div class="nav-item"><svg><use href="#i-sq"/></svg>Encounters</div><div class="nav-item"><svg><use href="#i-sq"/></svg>Payments</div><div class="nav-item"><svg><use href="#i-sq"/></svg>Billing</div><div class="nav-item"><svg><use href="#i-sq"/></svg>Reporting</div><div class="nav-item"><svg><use href="#i-sq"/></svg>Marketing</div><div class="nav-item"><svg><use href="#i-sq"/></svg>Forms</div><div class="nav-item"><svg><use href="#i-sq"/></svg>Lists</div><div class="nav-item"><svg><use href="#i-sq"/></svg>Admin</div>
  </nav>
  <header class="topbar"><div class="app-title">Forms App</div><div class="practice"><i></i>Sample healthcare practice</div><div class="welcome"><small>Welcome</small><b>Back,Test</b></div><div class="avatar" role="img" aria-label="User profile photo"></div><svg class="logout" viewBox="0 0 24 24"><path d="M3 3h9v3H6v12h6v3H3zM14 6l6 6-6 6v-4H9v-4h5z"/></svg></header>
  <div class="card">
    <div class="crumb">Home &nbsp;/&nbsp; Other</div>
    <div class="tabs">
      <div class="tab"><svg><use href="#i-office"/></svg><span>OFFICE</span></div><div class="tab"><svg><use href="#i-cal"/></svg><span>SCHEDULER</span></div><div class="tab"><svg><use href="#i-user"/></svg><span>PATIENT</span></div><div class="tab"><svg><use href="#i-news"/></svg><span>RELEASE</span></div><div class="tab"><svg><use href="#i-badge"/></svg><span>CERTIFICATES</span></div><div class="tab"><svg><use href="#i-shield"/></svg><span>INSURANCE</span></div><div class="tab active"><svg><use href="#i-list"/></svg><span>OTHER</span></div>
    </div>
    <div class="big-pill" style="top:150px;background:var(--crimson)"><svg viewBox="0 0 44 40"><circle cx="14" cy="7" r="5"/><path d="M6 26h34v5H6zM2 34h40v3H2zM10 14l12 6 8-2 2 4-10 3-14-5z"/></svg>FREE MASSAGE</div>
    <div class="big-pill" style="top:239px;background:var(--lime)"><svg viewBox="0 0 44 40"><path d="M8 36C4 26 10 14 24 12c-2 10-6 20-16 24zM22 36c0-10 6-20 18-22-1 11-8 20-18 22zM26 10c0-5 3-8 8-9 0 5-3 8-8 9z"/></svg>FREE VITAMINS</div>
  </div>
  <div class="footer">(c)2021 Companyname.All Rights Reserved &nbsp;|&nbsp; Privacy Policy &nbsp;|&nbsp; Terms and Use</div>
</section>

</body>
</html>
```